RWT Fittings Ltd Business Cards

We need a business card with our business logo. We provide window and door installations on high-rises in west coast British Colombia, Canada.

I would like my business information and details on one side of the card, and the other side the company name with logo

Target Market(s)

General Contractors

Industry/Entity Type

Construction

Contact Information for Business Card

one side i want my company name and logo in the dark theme logo that i provided

Requirements
Must have
• Marco Peltieri, 16045518293, RWTFittings@mailbox-demo.com, 1407-5194 Linden Row Burnaby BC, V5H 2K9, Owner & Manager

```html
<!DOCTYPE html>
<html lang="en">
<head>
<meta charset="utf-8">
<title>RWT Fittings Ltd — Business Card</title>
<link rel="stylesheet" href="https://fonts.googleapis.com/css2?family=Montserrat:wght@400;700&display=swap">
<style>
  :root {
    --backdrop: #cfd3d4;
    --card-light: #ffffff;
    --card-dark: #231f20;
    --brand-blue: #29a8e0;
    --edge-blue: #1f8fc0;
    --text-grey: #9a9a9a;
    --rule-grey: #a8a8a8;
  }
  * { box-sizing: border-box; margin: 0; padding: 0; }
  html, body {
    width: 1200px; height: 1200px; overflow: hidden;
    background: var(--backdrop);
    font-family: "Montserrat", Arial, sans-serif;
  }
  .sheet {
    position: relative; width: 1200px; height: 1200px;
    display: flex; flex-direction: column; align-items: center; justify-content: center; gap: 60px;
  }
  .card {
    position: relative; width: 700px; height: 400px;
    box-shadow: 0 14px 30px rgba(0,0,0,0.18);
  }
  /* front: contact side */
  .card--front { background: var(--card-light); border-bottom: 3px solid var(--edge-blue); }
  .holder { position: absolute; left: 60px; top: 120px; width: 230px; }
  .holder__name { color: var(--brand-blue); font-weight: 700; font-size: 34px; line-height: 1.1; }
  .holder__role { color: var(--text-grey); font-size: 19px; margin-top: 8px; }
  .divider { position: absolute; left: 318px; top: 120px; width: 2px; height: 90px; background: var(--rule-grey); }
  .contacts { position: absolute; left: 345px; top: 118px; list-style: none; }
  .contacts li {
    display: flex; align-items: center; gap: 10px;
    color: var(--text-grey); font-size: 16px; line-height: 30px;
  }
  .contacts svg { width: 16px; height: 16px; fill: var(--brand-blue); flex: none; }
  .address { position: absolute; left: 60px; bottom: 60px; color: var(--text-grey); font-size: 18px; }
  .mini-brand {
    position: absolute; right: 50px; top: 120px;
    display: flex; align-items: center; gap: 8px;
    color: var(--brand-blue); font-weight: 700; font-size: 15px;
  }
  .mini-brand__mark { width: 14px; height: 14px; background: var(--brand-blue); }
  /* back: brand side */
  .card--back {
    background: var(--card-dark); border-bottom: 6px solid var(--brand-blue);
    display: flex; align-items: center; justify-content: center; gap: 20px;
  }
  .brand__mark { width: 46px; height: 46px; background: var(--brand-blue); }
  .brand__name { color: var(--brand-blue); font-weight: 700; font-size: 52px; letter-spacing: 1px; }
</style>
</head>
<body>
<main class="sheet">
  <section class="card card--front" aria-label="Contact side">
    <div class="holder">
      <p class="holder__name">Marco Peltieri</p>
      <p class="holder__role">Owner &amp; Manager</p>
    </div>
    <div class="divider"></div>
    <ul class="contacts">
      <li><svg viewBox="0 0 24 24"><path d="M6.6 10.8a15 15 0 0 0 6.6 6.6l2.2-2.2a1 1 0 0 1 1-.25 11.4 11.4 0 0 0 3.6.57 1 1 0 0 1 1 1V20a1 1 0 0 1-1 1A17 17 0 0 1 3 4a1 1 0 0 1 1-1h3.5a1 1 0 0 1 1 1c0 1.25.2 2.45.57 3.57a1 1 0 0 1-.25 1z"/></svg>16045518293</li>
      <li><svg viewBox="0 0 24 24"><path d="M2 5h20v14H2z M2 5l10 8 10-8" fill="none" stroke="#29a8e0" stroke-width="2"/><path d="M2 5h20l-10 8z"/></svg>RWTFittings@mailbox-demo.com</li>
      <li><svg viewBox="0 0 24 24"><circle cx="12" cy="12" r="10" fill="none" stroke="#29a8e0" stroke-width="2"/><path d="M2 12h20M12 2c3 3 3 17 0 20M12 2c-3 3-3 17 0 20" fill="none" stroke="#29a8e0" stroke-width="2"/></svg>www.rwtfittings-demo.com</li>
    </ul>
    <p class="address">1407-5194 Linden Row Burnaby BC, V5H 2K9</p>
    <div class="mini-brand"><span class="mini-brand__mark"></span>RWT Fittings Ltd</div>
  </section>

  <section class="card card--back" aria-label="Brand side">
    <span class="brand__mark"></span>
    <span class="brand__name">RWT Fittings Ltd</span>
  </section>
</main>
</body>
</html>
```